Ductless Mini Split Business Website

Copper Fern Services is looking to design an eye catching educational website about installing Ductless mini splits.

Similar to this company.
https://www.halvikstream.com/

Coding

Coded - Design and coding required

```html
<!DOCTYPE html>
<html lang="en">
<head>
<meta charset="utf-8">
<title>Copper Fern Services – Ductless Experts</title>
<link href="https://fonts.googleapis.com/css2?family=Lato:wght@400;700;900&display=swap" rel="stylesheet">
<style>
:root{
  --yellow:#f2d200;
  --ink:#111111;
  --charcoal:#2b2b2b;
  --grey-text:#7a7a7a;
  --pale:#f0f0f0;
  --white:#ffffff;
}
*{box-sizing:border-box;margin:0;padding:0}
html,body{width:1200px;height:4093px;overflow:hidden;background:var(--white)}
body{font-family:'Lato',sans-serif;color:var(--ink)}
.page{position:relative;width:1200px;height:4093px;overflow:hidden}
.abs{position:absolute}
.btn{position:absolute;display:flex;align-items:center;justify-content:center;background:var(--charcoal);color:var(--yellow);border:3px solid var(--yellow);border-radius:30px;font-weight:900;font-size:12px;letter-spacing:.3px;text-transform:uppercase}
.h2{font-weight:900;font-size:38px;line-height:45px;text-transform:uppercase;letter-spacing:-.5px}
.body-copy{font-size:12px;line-height:19.7px;color:var(--grey-text)}

/* nav */
.topbar{left:0;top:0;width:1200px;height:45px;background:var(--charcoal)}
.topbar nav{position:absolute;left:260px;top:0;height:45px;display:flex;align-items:center;gap:25px;font-size:12px;color:var(--white)}
.topbar nav .active{color:var(--yellow)}
.topbar .phone{position:absolute;left:802px;top:6px;width:136px;height:33px;border:2px solid var(--yellow);border-radius:20px;color:var(--white);font-size:12px;display:flex;align-items:center;justify-content:center;gap:6px}

/* hero */
.hero{left:0;top:45px;width:1200px;height:690px}
.hero-photo{left:0;top:0;width:1200px;height:690px;background:
  radial-gradient(ellipse 150px 230px at 95px 390px,rgba(62,92,48,.85) 0,rgba(62,92,48,0) 100%),
  radial-gradient(ellipse 110px 150px at 770px 270px,rgba(205,176,150,.75) 0,rgba(205,176,150,0) 100%),
  radial-gradient(ellipse 130px 170px at 800px 520px,rgba(228,232,236,.9) 0,rgba(228,232,236,0) 100%),
  radial-gradient(ellipse 90px 30px at 600px 65px,rgba(190,200,205,.9) 0,rgba(190,200,205,0) 100%),
  linear-gradient(180deg,#eef0f1 0%,#e4e7e8 45%,#55585d 58%,#3d4045 72%,#9fa2a6 88%,#c7c8ca 100%)}
.hero-brand{left:0;top:118px;width:1200px;text-align:center}
.brand-name{display:inline-flex;align-items:center;gap:10px;font-weight:900;font-size:30px;color:var(--ink)}
.brand-dot{width:22px;height:22px;border-radius:50%;background:var(--yellow)}
.hero-tag{font-weight:700;font-size:22px;color:var(--ink);margin-top:8px;letter-spacing:.5px}
.hero-title{left:0;top:240px;width:1200px;text-align:center;font-weight:900;font-size:41px;color:var(--ink);-webkit-text-stroke:1px var(--yellow);letter-spacing:-.5px}
.hero-sub{left:410px;top:288px;width:380px;text-align:center;font-size:15px;line-height:22px;color:var(--ink)}
.hero-btn{left:502px;top:343px;width:194px;height:43px}

/* about */
.about-mark{left:164px;top:752px;width:62px;height:62px;border-radius:50%;background:var(--yellow);border:4px solid var(--ink)}
.about-title{left:162px;top:832px}
.about-sub{left:162px;top:885px;font-size:22px;color:var(--yellow);text-transform:uppercase}
.about-copy{left:162px;top:940px;width:370px}
.about-btn{left:162px;top:1087px;width:137px;height:44px}
.hex{position:absolute}
.play{left:825px;top:865px;width:60px;height:60px;border-radius:50%;border:3px solid var(--yellow);display:flex;align-items:center;justify-content:center}

/* why */
.answers-photo{left:170px;top:1265px;width:340px;height:380px;border-radius:170px 170px 0 0;background:
  radial-gradient(ellipse 60px 80px at 180px 120px,rgba(226,180,150,1) 0,rgba(226,180,150,0) 100%),
  radial-gradient(ellipse 70px 40px at 180px 30px,rgba(60,75,100,1) 0,rgba(60,75,100,0) 100%),
  linear-gradient(180deg,rgba(0,0,0,0) 0%,rgba(0,0,0,0) 40%,#4a6b9a 55%,#2d4a78 100%)}
.answers-circle{left:161px;top:1529px;width:374px;height:374px;border-radius:50%;background:#000;color:var(--white);text-align:center}
.answers-mark{width:46px;height:46px;border-radius:50%;background:var(--yellow);margin:50px auto 0}
.answers-title{font-weight:900;font-size:22px;margin-top:24px}
.answers-copy{font-size:12px;line-height:19.5px;color:#d8d8d8;width:300px;margin:12px auto 0}
.answers-btn{left:114px;top:265px;width:151px;height:45px;background:#000}
.why-title{left:600px;top:1442px}
.perk{position:absolute;left:599px;width:560px;height:90px}
.perk .icon{position:absolute;left:0;top:0;width:90px;height:90px;border-radius:50%;background:#000;display:flex;align-items:center;justify-content:center}
.perk h3{position:absolute;left:103px;top:0;font-weight:900;font-size:17px}
.perk p{position:absolute;left:103px;top:27px;width:320px}

/* help */
.help-title{left:0;top:1990px;width:1200px;text-align:center}
.service{position:absolute;width:196px;height:226px}
.service span{position:absolute;left:10px;right:10px;top:150px;text-align:center;font-weight:900;font-size:12px;line-height:15px;color:var(--yellow);text-transform:uppercase}
.sleep-photo{left:0;top:2280px;width:1200px;height:512px;background:
  radial-gradient(ellipse 260px 120px at 620px 300px,rgba(120,175,215,.8) 0,rgba(120,175,215,0) 100%),
  radial-gradient(ellipse 120px 90px at 860px 210px,rgba(214,180,140,.6) 0,rgba(214,180,140,0) 100%),
  radial-gradient(ellipse 140px 220px at 1140px 260px,rgba(150,155,165,.55) 0,rgba(150,155,165,0) 100%)}

/* reviews */
.review-title{left:600px;top:2936px}
.quote-mark{left:598px;top:3045px;font-weight:900;font-size:60px;line-height:60px;color:var(--yellow)}
.review-copy{left:600px;top:3090px;width:370px}
.review-name{left:600px;top:3190px;font-weight:900;font-size:12px}
.dots{left:600px;top:3234px;display:flex;gap:6px}

/* contact */
.contact-mark{left:570px;top:3390px;width:60px;height:60px;border-radius:50%;background:var(--ink);border:5px solid var(--white)}
.contact-title{left:0;top:3485px;width:1200px;text-align:center}
.field{position:absolute;border:1px solid var(--charcoal);font-size:11px;color:#444;padding:10px 9px}
.send-btn{left:516px;top:3767px;width:166px;height:43px}

/* footer */
.footer{left:0;top:3890px;width:1200px;height:203px;background:var(--charcoal);color:var(--white)}
.foot-brand{left:164px;top:46px;width:200px}
.foot-brand .brand-name{color:var(--yellow);font-size:16px;gap:7px}
.foot-brand .brand-dot{width:16px;height:16px}
.foot-tag{color:var(--yellow);font-weight:900;font-size:16px;margin-top:10px}
.foot-col{position:absolute;top:38px;font-size:11px;line-height:27px;color:#d0d0d0}
.foot-col .active{color:var(--yellow)}
.foot-contact{left:842px;top:38px;font-size:11px;color:#d0d0d0}
.foot-contact div{display:flex;gap:10px;align-items:flex-start;margin-bottom:11px}
.foot-contact .tel{color:var(--yellow);font-weight:900;font-size:15px}
.copyright{left:164px;top:174px;font-size:10px;color:#bdbdbd}
.socials{left:923px;top:168px;display:flex;gap:6px}
.socials i{width:26px;height:26px;border-radius:50%;border:2px solid var(--yellow)}
.socials i:first-child{background:var(--yellow)}
</style>
</head>
<body>
<div class="page">

  <!-- hero -->
  <section class="hero abs">
    <div class="hero-photo abs" role="img" aria-label="Smiling man working on a laptop on a grey sofa under a wall mounted ductless unit, with a potted plant"></div>
    <div class="hero-brand abs">
      <div class="brand-name"><span class="brand-dot"></span>Copper Fern Services</div>
      <div class="hero-tag">DUCTLESS EXPERTS</div>
    </div>
    <h1 class="hero-title abs">DUCTLESS IS BETTER</h1>
    <p class="hero-sub abs">Lorem Ipsum is simply dummy text of the printing and typesetting industry.</p>
    <a class="btn hero-btn">Get in touch with us</a>
  </section>
  <svg class="abs" style="left:0;top:560px" width="1200" height="180" viewBox="0 0 1200 180">
    <polygon points="0,23 600,163 1200,23 1200,180 0,180" fill="#fff"/>
    <polyline points="0,17 600,157 1200,17" fill="none" stroke="#f2d200" stroke-width="9"/>
  </svg>

  <!-- about -->
  <div class="about-mark abs"></div>
  <h2 class="h2 about-title abs">Copper Fern Services</h2>
  <div class="about-sub abs">Ductless Experts</div>
  <p class="body-copy about-copy abs">Lorem Ipsum is simply dummy text of the printing and typesetting industry. Lorem Ipsum has been the industry's standard dummy text ever since the 1500s, when an unknown printer took a galley of type and scrambled it to make a type specimen book. It has survived not only five centuries, but also the leap into electronic typesetting, remaining essentially unchanged.</p>
  <a class="btn about-btn">Read more</a>

  <!-- why / help background -->
  <svg class="abs" style="left:0;top:1112px" width="1200" height="1680" viewBox="0 0 1200 1680">
    <defs>
      <linearGradient id="roomGrad" x1="0" y1="0" x2="0" y2="1">
        <stop offset="0" stop-color="#a9c6d8"/>
        <stop offset=".45" stop-color="#dfe9ef"/>
        <stop offset=".75" stop-color="#f6f6f8"/>
        <stop offset="1" stop-color="#e3e6ec"/>
      </linearGradient>
    </defs>
    <polygon points="1200,30 1200,560 420,300" fill="#f0f0f0"/>
    <polygon points="0,143 1200,560 1200,1250 0,640" fill="#f2d200"/>
    <polygon points="0,640 1200,1250 1200,1680 0,1680" fill="url(#roomGrad)" role="img" aria-label="Wall mounted air conditioner above a woman sleeping peacefully in white bedding"/>
  </svg>
  <div class="sleep-photo abs" role="img" aria-label="Woman in a blue top asleep on white pillows"></div>
  <svg class="abs" style="left:0;top:1700px" width="1200" height="500" viewBox="0 0 1200 500">
    <defs><linearGradient id="acWall" x1="0" y1="0" x2="1" y2="1"><stop offset="0" stop-color="#bcd3e1"/><stop offset=".6" stop-color="#e8eef2"/><stop offset="1" stop-color="#cfdde7"/></linearGradient></defs>
    <polygon points="0,0 560,290 0,290" fill="url(#acWall)" role="img" aria-label="White air conditioner unit on a pale blue wall"/>
  </svg>

  <!-- hex photos (about) -->
  <svg class="hex" style="left:675px;top:694px" width="363" height="418" viewBox="0 0 100 115" role="img" aria-label="Two technicians in blue work uniforms in front of a van">
    <defs>
      <linearGradient id="techGrad" x1="0" y1="0" x2="0" y2="1"><stop offset="0" stop-color="#c9ccd0"/><stop offset=".25" stop-color="#8f9499"/><stop offset=".45" stop-color="#2e4a8c"/><stop offset="1" stop-color="#1a2c5e"/></linearGradient>
      <radialGradient id="techTone" cx=".5" cy=".2" r=".35"><stop offset="0" stop-color="#d9b296" stop-opacity=".55"/><stop offset="1" stop-color="#d9b296" stop-opacity="0"/></radialGradient>
    </defs>
    <polygon points="50,3 97,30 97,85 50,112 3,85 3,30" fill="url(#techGrad)" stroke="url(#techGrad)" stroke-width="6" stroke-linejoin="round"/>
    <polygon points="50,3 97,30 97,85 50,112 3,85 3,30" fill="url(#techTone)"/>
  </svg>
  <div class="play abs"><svg width="18" height="22" viewBox="0 0 18 22"><polygon points="2,1 17,11 2,21" fill="#f2d200"/></svg></div>
  <svg class="hex" style="left:610px;top:1061px" width="151" height="172" viewBox="0 0 100 115" role="img" aria-label="Technician servicing a wall unit">
    <defs><linearGradient id="svcWall" x1="0" y1="0" x2="0" y2="1"><stop offset="0" stop-color="#eceef0"/><stop offset=".4" stop-color="#5f6f8a"/><stop offset="1" stop-color="#2c4fa3"/></linearGradient></defs>
    <polygon points="50,4 96,30 96,85 50,111 4,85 4,30" fill="url(#svcWall)" stroke="url(#svcWall)" stroke-width="7" stroke-linejoin="round"/>
  </svg>
  <svg class="hex" style="left:760px;top:1196px" width="149" height="174" viewBox="0 0 100 115" role="img" aria-label="Family playing together at home">
    <defs><linearGradient id="famPlay" x1="0" y1="0" x2="1" y2="1"><stop offset="0" stop-color="#8a6f62"/><stop offset=".5" stop-color="#c98c86"/><stop offset="1" stop-color="#6e7f8f"/></linearGradient></defs>
    <polygon points="50,4 96,30 96,85 50,111 4,85 4,30" fill="url(#famPlay)" stroke="url(#famPlay)" stroke-width="7" stroke-linejoin="round"/>
  </svg>

  <!-- get some answers -->
  <div class="answers-photo abs" role="img" aria-label="Smiling technician in a cap and blue work shirt"></div>
  <div class="answers-circle abs">
    <div class="answers-mark"></div>
    <div class="answers-title">GET SOME ANSWERS</div>
    <p class="answers-copy">Lorem Ipsum is simply dummy text of the printing and typesetting industry. Lorem Ipsum has been the industry's standard dummy text ever since the 1500.</p>
    <a class="btn answers-btn">Ductless FAQ</a>
  </div>

  <!-- why choose -->
  <h2 class="h2 why-title abs">Why choose<br>Copper Fern?</h2>
  <div class="perk" style="top:1557px">
    <div class="icon"><svg width="40" height="44" viewBox="0 0 40 44" fill="none" stroke="#fff" stroke-width="2"><path d="M6 2h20l8 8v32H6z"/><circle cx="24" cy="24" r="8"/><path d="M11 14h10M11 34h8"/></svg></div>
    <h3>0% Financing for 60 months</h3>
    <p class="body-copy">Lorem Ipsum is simply dummy text of the printing and typesetting industry. Lorem Ipsum has been the industry.</p>
  </div>
  <div class="perk" style="top:1687px">
    <div class="icon"><svg width="48" height="40" viewBox="0 0 48 40" fill="none" stroke="#fff" stroke-width="2"><circle cx="24" cy="20" r="15"/><rect x="4" y="16" width="40" height="8" fill="#000"/></svg></div>
    <h3>365 Day, Money Back Guarantee</h3>
    <p class="body-copy">Lorem Ipsum is simply dummy text of the printing and typesetting industry. Lorem Ipsum has been the industry.</p>
  </div>
  <div class="perk" style="top:1814px">
    <div class="icon"><svg width="40" height="44" viewBox="0 0 40 44" fill="none" stroke="#fff" stroke-width="2"><path d="M10 14a10 10 0 0 1 20 0z"/><circle cx="20" cy="20" r="6"/><path d="M6 42v-8a8 8 0 0 1 8-8h12a8 8 0 0 1 8 8v8"/></svg></div>
    <h3>We Are the Experts in Ductless Services</h3>
    <p class="body-copy">Lorem Ipsum is simply dummy text of the printing and typesetting industry. Lorem Ipsum has been the industry.</p>
  </div>

  <!-- how we can help -->
  <h2 class="h2 help-title abs">How we can help you?</h2>
  <svg width="0" height="0" style="position:absolute">
    <defs>
      <linearGradient id="g1" x1="0" y1="0" x2="0" y2="1"><stop offset="0" stop-color="#c4c7cb"/><stop offset=".45" stop-color="#6d7177"/><stop offset="1" stop-color="#1d2230"/></linearGradient>
      <linearGradient id="g2" x1="0" y1="0" x2="0" y2="1"><stop offset="0" stop-color="#b7b0aa"/><stop offset=".45" stop-color="#a6393a"/><stop offset="1" stop-color="#25202a"/></linearGradient>
      <linearGradient id="g3" x1="0" y1="0" x2="0" y2="1"><stop offset="0" stop-color="#3a4660"/><stop offset=".45" stop-color="#9c8a70"/><stop offset="1" stop-color="#1b2333"/></linearGradient>
      <linearGradient id="g4" x1="0" y1="0" x2="0" y2="1"><stop offset="0" stop-color="#e2e4e6"/><stop offset=".45" stop-color="#8c8f96"/><stop offset="1" stop-color="#1d2437"/></linearGradient>
      <linearGradient id="g5" x1="0" y1="0" x2="0" y2="1"><stop offset="0" stop-color="#d8dadc"/><stop offset=".45" stop-color="#445a8c"/><stop offset="1" stop-color="#1b2333"/></linearGradient>
      <linearGradient id="g6" x1="0" y1="0" x2="0" y2="1"><stop offset="0" stop-color="#e4e6e8"/><stop offset=".45" stop-color="#8a7a64"/><stop offset="1" stop-color="#1e2536"/></linearGradient>
      <linearGradient id="g7" x1="0" y1="0" x2="0" y2="1"><stop offset="0" stop-color="#f0f1f2"/><stop offset=".45" stop-color="#9a9ca2"/><stop offset="1" stop-color="#202634"/></linearGradient>
      <linearGradient id="g8" x1="0" y1="0" x2="0" y2="1"><stop offset="0" stop-color="#e6e2da"/><stop offset=".45" stop-color="#8b7358"/><stop offset="1" stop-color="#1f2534"/></linearGradient>
    </defs>
  </svg>
  <div class="service" style="left:160px;top:2066px"><svg width="196" height="226" viewBox="0 0 100 115" role="img" aria-label="Outdoor heat pump fan unit"><polygon points="50,3 97,30 97,85 50,112 3,85 3,30" fill="url(#g1)" stroke="#f2d200" stroke-width="2.5" stroke-linejoin="round"/></svg><span>Baseboard heat<br>replacement</span></div>
  <div class="service" style="left:389px;top:2066px"><svg width="196" height="226" viewBox="0 0 100 115" role="img" aria-label="Living room with red sofa"><polygon points="50,3 97,30 97,85 50,112 3,85 3,30" fill="url(#g2)" stroke="#f2d200" stroke-width="2.5" stroke-linejoin="round"/></svg><span>Ductless for<br>additions &amp; remodels</span></div>
  <div class="service" style="left:617px;top:2066px"><svg width="196" height="226" viewBox="0 0 100 115" role="img" aria-label="Hands filling in a form with a pen"><polygon points="50,3 97,30 97,85 50,112 3,85 3,30" fill="url(#g3)" stroke="#f2d200" stroke-width="2.5" stroke-linejoin="round"/></svg><span>Ductless heat pump<br>FAQ</span></div>
  <div class="service" style="left:844px;top:2066px"><svg width="196" height="226" viewBox="0 0 100 115" role="img" aria-label="Technician installing an indoor unit"><polygon points="50,3 97,30 97,85 50,112 3,85 3,30" fill="url(#g4)" stroke="#f2d200" stroke-width="2.5" stroke-linejoin="round"/></svg><span>Ductless installation</span></div>
  <div class="service" style="left:160px;top:2320px"><svg width="196" height="226" viewBox="0 0 100 115" role="img" aria-label="Technician maintaining a wall unit"><polygon points="50,3 97,30 97,85 50,112 3,85 3,30" fill="url(#g5)" stroke="#f2d200" stroke-width="2.5" stroke-linejoin="round"/></svg><span>Ductless<br>maintenance</span></div>
  <div class="service" style="left:389px;top:2320px"><svg width="196" height="226" viewBox="0 0 100 115" role="img" aria-label="Technician repairing a unit while a customer watches"><polygon points="50,3 97,30 97,85 50,112 3,85 3,30" fill="url(#g6)" stroke="#f2d200" stroke-width="2.5" stroke-linejoin="round"/></svg><span>Ductless repairs</span></div>
  <div class="service" style="left:617px;top:2320px"><svg width="196" height="226" viewBox="0 0 100 115" role="img" aria-label="Close view of an indoor ductless unit"><polygon points="50,3 97,30 97,85 50,112 3,85 3,30" fill="url(#g7)" stroke="#f2d200" stroke-width="2.5" stroke-linejoin="round"/></svg><span>Ductless warranty</span></div>
  <div class="service" style="left:844px;top:2320px"><svg width="196" height="226" viewBox="0 0 100 115" role="img" aria-label="Open plan dining room"><polygon points="50,3 97,30 97,85 50,112 3,85 3,30" fill="url(#g8)" stroke="#f2d200" stroke-width="2.5" stroke-linejoin="round"/></svg><span>Whole house ductless</span></div>

  <!-- testimonials -->
  <svg class="hex" style="left:160px;top:2863px" width="364" height="423" viewBox="0 0 100 115" role="img" aria-label="Happy family of three sitting together">
    <defs>
      <linearGradient id="famGrad" x1="0" y1="0" x2="1" y2="1"><stop offset="0" stop-color="#eceef2"/><stop offset=".35" stop-color="#caa48c"/><stop offset=".6" stop-color="#e9d2c6"/><stop offset="1" stop-color="#6f8fc4"/></linearGradient>
      <radialGradient id="famHair" cx=".6" cy=".3" r=".25"><stop offset="0" stop-color="#d9b86a" stop-opacity=".6"/><stop offset="1" stop-color="#d9b86a" stop-opacity="0"/></radialGradient>
    </defs>
    <polygon points="50,2 98,29 98,86 50,113 2,86 2,29" fill="url(#famGrad)" stroke="#f2d200" stroke-width="1.2" stroke-linejoin="round"/>
    <polygon points="50,2 98,29 98,86 50,113 2,86 2,29" fill="url(#famHair)"/>
  </svg>
  <h2 class="h2 review-title abs">What our clients<br>have to say</h2>
  <div class="quote-mark abs">&ldquo;</div>
  <p class="body-copy review-copy abs">Lorem Ipsum is simply dummy text of the printing and typesetting industry. Lorem Ipsum has been the industry's standard dummy text ever since the 1500s, when an unknown printer took a galley of type and scrambled it to make a type specimen book.</p>
  <div class="review-name abs">- CLIENTS NAME</div>
  <div class="dots abs">
    <svg width="17" height="19" viewBox="0 0 17 19"><polygon points="8.5,1 16,5 16,14 8.5,18 1,14 1,5" fill="#111" stroke="#111"/></svg>
    <svg width="17" height="19" viewBox="0 0 17 19"><polygon points="8.5,1 16,5 16,14 8.5,18 1,14 1,5" fill="none" stroke="#111"/></svg>
    <svg width="17" height="19" viewBox="0 0 17 19"><polygon points="8.5,1 16,5 16,14 8.5,18 1,14 1,5" fill="none" stroke="#111"/></svg>
    <svg width="17" height="19" viewBox="0 0 17 19"><polygon points="8.5,1 16,5 16,14 8.5,18 1,14 1,5" fill="none" stroke="#111"/></svg>
  </div>

  <!-- contact -->
  <svg class="abs" style="left:0;top:3337px" width="1200" height="555" viewBox="0 0 1200 555">
    <polygon points="0,127 600,0 1200,127 1200,555 0,555" fill="#f2d200"/>
  </svg>
  <div class="contact-mark abs"></div>
  <h2 class="h2 contact-title abs">Get in touch with us</h2>
  <div class="field" style="left:323px;top:3560px;width:268px;height:35px">Enter Name</div>
  <div class="field" style="left:605px;top:3560px;width:271px;height:35px">Enter Contact No.</div>
  <div class="field" style="left:323px;top:3612px;width:553px;height:35px">Enter Email</div>
  <div class="field" style="left:323px;top:3664px;width:553px;height:88px">Enter Email</div>
  <a class="btn send-btn">Send message</a>

  <!-- footer -->
  <footer class="footer abs">
    <div class="foot-brand abs">
      <div class="brand-name"><span class="brand-dot"></span>Copper Fern Services</div>
      <div class="foot-tag">DUCTLESS EXPERTS</div>
    </div>
    <div class="foot-col" style="left:389px"><div class="active">Home</div><div>About Us</div><div>Ductless Heat pumps</div><div>Faq</div></div>
    <div class="foot-col" style="left:617px"><div>Financing</div><div>Reviews</div><div>Contact Us</div></div>
    <div class="foot-contact abs">
      <div class="tel"><svg width="14" height="14" viewBox="0 0 24 24"><path fill="#fff" d="M6.6 10.8a15 15 0 0 0 6.6 6.6l2.2-2.2c.3-.3.7-.4 1-.2 1.1.4 2.3.6 3.6.6.6 0 1 .4 1 1V20c0 .6-.4 1-1 1A17 17 0 0 1 3 4c0-.6.4-1 1-1h3.5c.6 0 1 .4 1 1 0 1.3.2 2.5.6 3.6.1.3 0 .7-.2 1z"/></svg>123 456 7890</div>
      <div><svg width="14" height="11" viewBox="0 0 14 11"><rect width="14" height="11" rx="1" fill="#fff"/><path d="M0 1l7 5 7-5" fill="none" stroke="#2b2b2b" stroke-width="1.3"/></svg>info@copperfernservices.com</div>
      <div><svg width="12" height="16" viewBox="0 0 12 16"><path d="M6 0a6 6 0 0 1 6 6c0 4-6 10-6 10S0 10 0 6a6 6 0 0 1 6-6z" fill="#fff"/><circle cx="6" cy="6" r="2.2" fill="#2b2b2b"/></svg><span>Lorem Ipsum is simply dummy<br>text of the printing</span></div>
    </div>
    <div class="copyright abs">&copy; Copper Fern Services - 2019. All Rights Reserved.</div>
    <div class="socials abs"><i></i><i></i><i></i><i></i></div>
  </footer>

  <!-- top bar -->
  <header class="topbar abs">
    <nav><span class="active">Home</span><span>About Us</span><span>Ductless Heat pumps</span><span>Faq</span><span>Financing</span><span>Reviews</span><span>Contact Us</span></nav>
    <div class="phone"><svg width="12" height="12" viewBox="0 0 24 24"><path fill="#fff" d="M6.6 10.8a15 15 0 0 0 6.6 6.6l2.2-2.2c.3-.3.7-.4 1-.2 1.1.4 2.3.6 3.6.6.6 0 1 .4 1 1V20c0 .6-.4 1-1 1A17 17 0 0 1 3 4c0-.6.4-1 1-1h3.5c.6 0 1 .4 1 1 0 1.3.2 2.5.6 3.6.1.3 0 .7-.2 1z"/></svg>123 456 7890</div>
  </header>

</div>
</body>
</html>
```